Moravel Aesthetic Doctor

I require an elegant, luxurious looking business card for my aesthetic business. I am a doctor and that will set me aside from competitors. I am planning to provide home and spa based treatments to clients with high expectations. I have attached my logo.

```html
<!DOCTYPE html>
<html lang="en">
<head>
<meta charset="utf-8">
<title>Moravel Aesthetic Doctor – Business Card</title>
<link rel="stylesheet" href="https://fonts.googleapis.com/css2?family=Open+Sans:wght@400;600;700&display=swap">
<style>
  :root {
    --backdrop: #cfd0d2;
    --card-white: #ffffff;
    --brand-blue: #1565c0;
    --brand-blue-deep: #0d4fa3;
    --accent-blue: #4aa8e0;
    --text-dark: #333a44;
    --text-grey: #9a9ea4;
    --divider: #b5b8bc;
    --on-blue: #ffffff;
  }
  * { margin: 0; padding: 0; box-sizing: border-box; }
  html, body { width: 1200px; height: 800px; overflow: hidden; }
  body {
    background: var(--backdrop);
    font-family: "Open Sans", Arial, sans-serif;
    display: flex;
    align-items: center;
    justify-content: center;
    gap: 40px;
  }
  .card {
    width: 540px;
    height: 310px;
    position: relative;
    box-shadow: 0 10px 24px rgba(0,0,0,0.18);
  }

  /* Front */
  .card-front {
    background: var(--card-white);
    display: flex;
    align-items: center;
    padding: 0 30px;
  }
  .brand-block {
    display: flex;
    align-items: center;
    gap: 12px;
    width: 240px;
  }
  .brand-dot {
    width: 46px; height: 46px;
    border-radius: 50%;
    border: 2px solid var(--accent-blue);
    flex-shrink: 0;
  }
  .brand-name {
    color: var(--accent-blue);
    font-weight: 400;
    line-height: 1.1;
  }
  .brand-name .brand-main { display: block; font-size: 34px; letter-spacing: 2px; }
  .brand-name .brand-sub { display: block; font-size: 13px; letter-spacing: 1.5px; }
  .divider {
    width: 1px;
    height: 120px;
    background: var(--divider);
    margin: 0 18px 0 6px;
  }
  .person-block { color: var(--text-dark); }
  .person-name {
    color: var(--brand-blue);
    font-weight: 700;
    font-size: 19px;
  }
  .person-name .credentials { font-size: 11px; font-weight: 600; }
  .person-title {
    color: var(--text-grey);
    font-size: 10.5px;
    margin-bottom: 12px;
  }
  .contact-list { list-style: none; font-size: 13px; line-height: 1.55; }
  .contact-list li { display: flex; align-items: center; gap: 7px; }
  .contact-list svg { width: 11px; height: 11px; fill: var(--brand-blue-deep); }

  /* Back */
  .card-back {
    background: linear-gradient(160deg, #1a6fce 0%, var(--brand-blue) 55%, var(--brand-blue-deep) 100%);
    color: var(--on-blue);
    text-align: center;
  }
  .social-dots {
    position: absolute;
    top: 16px; right: 18px;
    display: flex; gap: 6px;
  }
  .social-dots span {
    width: 20px; height: 20px;
    border-radius: 50%;
    background: var(--on-blue);
  }
  .back-mark {
    position: absolute;
    top: 56px; left: 50%;
    transform: translateX(-50%);
    display: flex; align-items: center; gap: 12px;
  }
  .back-mark .mark-circle {
    width: 120px; height: 120px;
    border-radius: 50%;
    border: 3px solid var(--brand-blue-deep);
    display: flex; align-items: center; justify-content: center;
    color: var(--on-blue);
    font-size: 18px;
    font-weight: 400;
    letter-spacing: 2px;
  }
  .treatments {
    position: absolute;
    left: 0; right: 0; bottom: 34px;
    font-size: 13px;
    line-height: 1.45;
  }
  .treatments h2 {
    font-size: 13px;
    font-weight: 700;
    letter-spacing: 0.3px;
  }
  .treatments .sep { margin: 0 5px; }
</style>
</head>
<body>

  <section class="card card-front">
    <div class="brand-block">
      <span class="brand-dot"></span>
      <div class="brand-name">
        <span class="brand-main">MORAVEL</span>
        <span class="brand-sub">AESTHETIC DOCTOR</span>
      </div>
    </div>
    <div class="divider"></div>
    <div class="person-block">
      <p class="person-name">Dr Elise Varnholt <span class="credentials">MRCPCH MD</span></p>
      <p class="person-title">Australasian Diploma of Aesthetic Medicine</p>
      <ul class="contact-list">
        <li>
          <svg viewBox="0 0 24 24" aria-hidden="true"><path d="M6.6 10.8a15.2 15.2 0 0 0 6.6 6.6l2.2-2.2c.3-.3.7-.4 1-.2 1.1.4 2.3.6 3.6.6.6 0 1 .4 1 1V20c0 .6-.4 1-1 1A17 17 0 0 1 3 4c0-.6.4-1 1-1h3.5c.6 0 1 .4 1 1 0 1.3.2 2.5.6 3.6.1.3 0 .7-.2 1z"/></svg>
          0800 555 014
        </li>
        <li>
          <svg viewBox="0 0 24 24" aria-hidden="true"><path d="M2 5h20v14H2z M2 5l10 8 10-8" fill="none" stroke="#0d4fa3" stroke-width="2.5"/></svg>
          elise@moravel.co.nz
        </li>
        <li>
          <svg viewBox="0 0 24 24" aria-hidden="true"><circle cx="12" cy="12" r="9" fill="none" stroke="#0d4fa3" stroke-width="2.5"/><path d="M3 12h18M12 3c3 3 3 15 0 18M12 3c-3 3-3 15 0 18" fill="none" stroke="#0d4fa3" stroke-width="2"/></svg>
          www.moravel.co.nz
        </li>
      </ul>
    </div>
  </section>

  <section class="card card-back">
    <div class="social-dots" aria-hidden="true"><span></span><span></span></div>
    <div class="back-mark">
      <div class="mark-circle">MORAVEL</div>
    </div>
    <div class="treatments">
      <h2>HOME &amp; SPA BASED TREATMENTS</h2>
      <p>Dermal injectables<span class="sep">●</span>Plasma facials<span class="sep">●</span>Microneedling</p>
      <p>Skin boosters<span class="sep">●</span>Excessive sweating</p>
    </div>
  </section>

</body>
</html>
```